Poloshirt Packaging

We need a very attractive packaging design for our poloshirts. We are wholesaler of the schoolwear market. See what we currently have. I dont want any specific sizing put on the packaging. One design for all poloshirts (2 sides).
our logo is attached aswell

Target Market(s)

Parents

Requirements
Must have
• Our logo
Should not have
• size or age

```html
<!DOCTYPE html>
<html lang="en">
<head>
<meta charset="utf-8">
<title>Uniforma Poloshirt Packaging</title>
<link rel="stylesheet" href="https://fonts.googleapis.com/css2?family=Montserrat:wght@600;700&family=Roboto+Condensed:wght@400;700&display=swap">
<style>
  :root {
    --navy: #1b365f;
    --red: #e2202f;
    --band-red: #e5332a;
    --band-orange: #f39220;
    --band-yellow: #fcdc00;
    --ink: #2b2b2b;
    --paper: #ffffff;
    --frame: #3a3a3a;
  }
  * { margin: 0; padding: 0; box-sizing: border-box; }
  html, body { width: 849px; height: 1200px; overflow: hidden; background: var(--paper); }
  .package-face {
    position: relative;
    width: 849px;
    height: 1200px;
    background: var(--paper);
    border: 1px solid var(--frame);
    overflow: hidden;
  }
  .brand-name {
    position: absolute;
    top: 334px;
    left: 0;
    width: 100%;
    text-align: center;
    font-family: "Montserrat", sans-serif;
    font-weight: 700;
    font-size: 98px;
    line-height: 1;
    letter-spacing: 1px;
    color: var(--navy);
  }
  .did-you-know {
    position: absolute;
    top: 678px;
    left: 0;
    width: 100%;
    text-align: center;
    font-family: "Roboto Condensed", sans-serif;
    font-size: 15.5px;
    line-height: 24.4px;
    color: var(--ink);
  }
  .did-you-know h2 {
    font-size: 15.5px;
    font-weight: 700;
    color: #1a1a1a;
  }
  .did-you-know p { font-weight: 400; }
  .thanks-band {
    position: absolute;
    top: 829px;
    left: 0;
    width: 100%;
    height: 37px;
    background: linear-gradient(90deg, var(--band-red) 0%, var(--band-orange) 50%, var(--band-yellow) 100%);
    display: flex;
    align-items: center;
    justify-content: center;
    font-family: "Roboto Condensed", sans-serif;
    font-size: 15px;
    color: #2a1d10;
  }
  .product-name {
    position: absolute;
    top: 938px;
    left: 0;
    width: 100%;
    text-align: center;
    font-family: "Montserrat", sans-serif;
    font-weight: 700;
    font-size: 62px;
    line-height: 1;
    letter-spacing: 1px;
    color: var(--red);
  }
</style>
</head>
<body>
  <main class="package-face">
    <h1 class="brand-name">Uniforma</h1>

    <section class="did-you-know">
      <h2>Did you know</h2>
      <p>This Poloshirt Is Sold In 12 Colours</p>
      <p>Reactive Dyed For Superb Colour Fastness</p>
      <p>A Superior Weight Of 210gms</p>
      <p>Strengthened With Twin Needle Stitching</p>
    </section>

    <div class="thanks-band">Thanks You for Buying Our Product and Ask your Local Supplier abt the Rest Of Uniforma Range</div>

    <div class="product-name">POLOSHIRT</div>
  </main>
</body>
</html>
```